professional business card design for technology company

We are a small technology consulting firm, specialising in consulting based around Cloud and Managed services. Our colour scheme is yellow, blue and white, as you can see in the logos. Although we are based in melbourne australia, due to the nature of our work, our clients can be located anywhere. We are looking for a clean, professional, positive look - similar to our company logo

Target Market(s)

small business

Industry/Entity Type

Business

Contact Information for Business Card

eye catching, designed to incorporate some level of raised printing. Must contain website address, phone number, name and job title

Requirements
Must have
• Logo (attached) - use of the same colour scheme

```html
<!DOCTYPE html>
<html lang="en">
<head>
<meta charset="utf-8">
<title>Cloudara Business Card</title>
<link rel="stylesheet" href="https://fonts.googleapis.com/css2?family=Lato:wght@400;700;900&display=swap">
<style>
  :root {
    --bg: #2a2a2a;
    --card-dark: #454545;
    --card-light: #ffffff;
    --blue: #2c92d0;
    --yellow: #e6c21a;
    --ink: #1e1e1e;
    --grey: #4a4a4a;
    --band-grey: #5a5a5a;
  }
  * { margin: 0; padding: 0; box-sizing: border-box; }
  html, body { width: 1200px; height: 873px; overflow: hidden; }
  body {
    background: var(--bg);
    font-family: 'Lato', sans-serif;
    position: relative;
  }
  .card {
    position: absolute;
    left: 320px;
    width: 560px;
    height: 320px;
    border-radius: 3px;
    overflow: hidden;
    box-shadow: 0 12px 30px rgba(0,0,0,.45);
  }
  .card--front { top: 88px; background: var(--card-dark); }
  .card--back { top: 465px; background: var(--card-light); }

  .brand { position: absolute; display: flex; align-items: center; gap: 14px; }
  .brand__dot { width: 40px; height: 40px; border-radius: 50%; background: var(--blue); }
  .brand__name { font-weight: 900; letter-spacing: -0.5px; }
  .card--front .brand { left: 120px; top: 118px; }
  .card--front .brand__name { color: #f4f4f4; font-size: 58px; }
  .card--back .brand { left: 40px; top: 100px; gap: 10px; }
  .card--back .brand__dot { width: 30px; height: 30px; }
  .card--back .brand__name { color: var(--grey); font-size: 40px; }

  .slogan {
    position: absolute; right: 40px; top: 180px;
    color: var(--yellow); font-weight: 700; font-size: 14px;
  }
  .website {
    position: absolute; left: 40px; bottom: 32px;
    color: var(--blue); font-weight: 700; font-size: 15px;
  }
  .front-divider {
    position: absolute; left: 300px; bottom: 30px; width: 2px; height: 34px;
    background: linear-gradient(to bottom, transparent, #d8d8d8, transparent);
  }

  .address {
    position: absolute; left: 40px; top: 214px;
    color: var(--blue); font-weight: 900; font-size: 15px; line-height: 1.35;
  }
  .back-divider {
    position: absolute; left: 300px; top: 20px; width: 3px; height: 210px;
    background: linear-gradient(to bottom, rgba(44,146,208,0), var(--blue) 50%, rgba(44,146,208,0));
  }
  .person { position: absolute; left: 330px; top: 34px; }
  .person__name { color: var(--blue); font-weight: 900; font-size: 19px; }
  .person__title { color: var(--ink); font-weight: 700; font-size: 13px; margin-top: 2px; }

  .contacts { position: absolute; left: 330px; top: 130px; list-style: none; }
  .contacts li {
    display: flex; align-items: center; gap: 10px;
    font-size: 15px; color: var(--ink); margin-bottom: 7px;
  }
  .contacts .icon {
    width: 22px; height: 22px; border-radius: 50%; background: var(--yellow);
    display: flex; align-items: center; justify-content: center;
  }
  .bands { position: absolute; left: 0; bottom: 0; width: 560px; height: 80px; }
</style>
</head>
<body>
  <section class="card card--front" aria-label="Card front">
    <div class="brand">
      <span class="brand__dot"></span>
      <span class="brand__name">Cloudara</span>
    </div>
    <p class="slogan">Your Slogan / Tagline Here</p>
    <span class="front-divider"></span>
    <p class="website">www.cloudara.com</p>
  </section>

  <section class="card card--back" aria-label="Card back">
    <div class="brand">
      <span class="brand__dot"></span>
      <span class="brand__name">Cloudara</span>
    </div>
    <p class="address">2840 Harbor Lane, Suite 12<br>Brookfield, Ohio 44403</p>
    <span class="back-divider"></span>
    <div class="person">
      <p class="person__name">Martin K. Hale</p>
      <p class="person__title">Broker / Owner</p>
    </div>
    <ul class="contacts">
      <li><span class="icon"><svg width="12" height="12" viewBox="0 0 24 24"><path fill="#333" d="M6.6 10.8a15 15 0 0 0 6.6 6.6l2.2-2.2c.3-.3.7-.4 1-.2 1.1.4 2.3.6 3.6.6.6 0 1 .4 1 1V20c0 .6-.4 1-1 1A17 17 0 0 1 3 4c0-.6.4-1 1-1h3.5c.6 0 1 .4 1 1 0 1.3.2 2.5.6 3.6.1.3 0 .7-.2 1z"/></svg></span>555-210-4830</li>
      <li><span class="icon"><svg width="10" height="13" viewBox="0 0 10 14"><rect x="1" y="0.5" width="8" height="13" rx="1.5" fill="none" stroke="#333" stroke-width="1.4"/><circle cx="5" cy="11" r="0.9" fill="#333"/></svg></span>555-318-6027</li>
      <li><span class="icon"><svg width="12" height="9" viewBox="0 0 12 9"><rect x="0.5" y="0.5" width="11" height="8" fill="none" stroke="#333"/><path d="M0.5 0.5 6 5l5.5-4.5" fill="none" stroke="#333"/></svg></span>mhale@cloudara.com</li>
    </ul>
    <svg class="bands" viewBox="0 0 560 80" aria-hidden="true">
      <path d="M0 62 L330 62 Q345 62 352 70 L352 80 L0 80 Z" fill="var(--band-grey)"/>
      <path d="M560 14 L420 30 Q370 36 350 62 Q345 70 345 80 L560 80 Z" fill="var(--blue)"/>
      <path d="M560 26 L425 40 Q385 44 368 62 Q360 72 360 80 L560 80 Z" fill="#ffffff"/>
    </svg>
  </section>
</body>
</html>
```